Tech business card design

We need an amazing business card design for our new business 'Pexla' a marketing tech startup based in Sydney, Australia. We provide an online marketplace for businesses to search and buy advertising media, connect with service providers and learn more about marketing. We wish to communicate 'cool tech', reliability and professionalism and design based around our logo.

Target Market(s)

Business Owners

Contact Information for Business Card

Name
Position
Email Address
Website
Phone Number

Font styles to use
Other font styles liked:
• Avenir & Avenir Next

Colors

Designer to choose colors to be used in the design.

```html
<!DOCTYPE html>
<html lang="en">
<head>
<meta charset="utf-8">
<title>Pexla — Business Card</title>
<link href="https://fonts.googleapis.com/css2?family=Lato:wght@300;400;700;900&display=swap" rel="stylesheet">
<style>
  :root {
    --backdrop: #3b322d;
    --card: #0e0e0e;
    --card-edge: #1c1c1c;
    --silver: #d8dadd;
    --text-strong: #f2f2f2;
    --text-soft: #9a9a9a;
    --divider: #2e2e2e;
  }
  * { margin: 0; padding: 0; box-sizing: border-box; }
  html, body {
    width: 1200px; height: 844px; overflow: hidden;
    background: var(--backdrop);
    font-family: "Lato", "Helvetica Neue", Arial, sans-serif;
  }
  .stage {
    position: relative; width: 1200px; height: 844px;
    display: flex; align-items: center; justify-content: center; gap: 40px;
  }
  .card {
    position: relative; width: 520px; height: 300px;
    background: var(--card);
    border: 1px solid var(--card-edge);
    box-shadow: 0 18px 40px rgba(0,0,0,0.45);
  }
  .wordmark {
    color: var(--silver);
    font-weight: 900;
    letter-spacing: -1px;
    line-height: 1;
  }
  /* Back side: wordmark + contact details */
  .card-back .wordmark {
    position: absolute; left: 34px; top: 168px; font-size: 62px;
  }
  .card-back .divider {
    position: absolute; left: 290px; top: 30px; width: 1px; height: 170px;
    background: var(--divider);
  }
  .contact {
    position: absolute; left: 312px; top: 44px;
  }
  .contact-name {
    color: var(--text-strong); font-weight: 700; font-size: 15px;
    letter-spacing: 0.6px; text-transform: uppercase;
  }
  .contact-role {
    color: var(--text-soft); font-weight: 300; font-size: 13px; margin-top: 2px;
  }
  .contact-list { list-style: none; margin-top: 14px; }
  .contact-list li {
    display: flex; align-items: center; gap: 8px;
    color: var(--text-soft); font-size: 13px; font-weight: 400;
    margin-bottom: 4px;
  }
  .contact-list svg { width: 11px; height: 11px; fill: var(--text-strong); flex: none; }
  /* Front side: centred wordmark */
  .card-front { display: flex; align-items: center; justify-content: center; }
  .card-front .wordmark { font-size: 78px; }
</style>
</head>
<body>
<main class="stage">
  <section class="card card-back" aria-label="Card back with contact details">
    <div class="wordmark">pexla</div>
    <div class="divider"></div>
    <div class="contact">
      <p class="contact-name">Daniel Hart</p>
      <p class="contact-role">Managing Director</p>
      <ul class="contact-list">
        <li>
          <svg viewBox="0 0 12 12" aria-hidden="true"><path d="M1 3.5C1 2 2 1 3 1l1.5 2.2-1 1.2c.6 1.4 1.7 2.5 3.1 3.1l1.2-1L11 8c0 1-1 2-2.5 2C4.4 10 1 6.6 1 3.5z"/></svg>
          02-9481 3370
        </li>
        <li>
          <svg viewBox="0 0 12 12" aria-hidden="true"><path d="M1 2.5h10v7H1z M1.6 3l4.4 3.4L10.4 3" fill="none" stroke="#f2f2f2" stroke-width="1"/></svg>
          hello@pexlamedia.com
        </li>
        <li>
          <svg viewBox="0 0 12 12" aria-hidden="true"><circle cx="6" cy="6" r="5"/></svg>
          www.pexlamedia.com
        </li>
      </ul>
    </div>
  </section>
  <section class="card card-front" aria-label="Card front">
    <div class="wordmark">pexla</div>
  </section>
</main>
</body>
</html>
```